Redesign Website - Current one too plain

The description is in the uploaded file. Please let me know if you need any more information. I'd prefer it if someone could implement the design to a WordPress site but the best design will win, regardless.
I would like the forms to look nice as well
UPDATE:
I don't think we can use the images that I provided, I think they make the site look a bit 'cheap' and I really don't know how to replace them. One thought I have had is to make the "Simple, Unique, Effective" a second feature on the right side of the page with the search on the left
Target Market(s)
Small companies, private sellers of cars and people who rent their caravan/holiday home out
Industry/Entity Type
Advertising
Number of Pages Required
3 page
Colors
Designer to choose colors to be used in the design.
Look and feel
Each slider illustrates characteristics of the customer's brand and the style your logo design should communicate.

```html
<!DOCTYPE html>
<html lang="en">
<head>
<meta charset="utf-8">
<title>KODRA – Advertise with a code</title>
<link href="https://fonts.googleapis.com/css2?family=Mulish:wght@300;400;600;700;800;900&display=swap" rel="stylesheet">
<style>
:root{
  --yellow:#fff200;
  --ink:#111111;
  --text:#333333;
  --muted:#555555;
  --navy:#182c45;
  --navy-deep:#13253b;
  --white:#ffffff;
  --grey-band:#f5f4f4;
  --grey-testi:#f1f1f1;
  --footer:#1d1d1d;
  --line:#3a3a3a;
}
*{box-sizing:border-box;margin:0;padding:0}
html,body{width:1200px;height:2998px;overflow:hidden}
body{font-family:'Mulish',sans-serif;color:var(--text);background:var(--white);position:relative}
.abs{position:absolute}
.btn{position:absolute;display:flex;align-items:center;justify-content:center;border-radius:20px;font-size:15px;font-weight:500;color:var(--ink);background:var(--yellow)}
.btn-white{background:var(--white)}
.brand{position:absolute;display:flex;align-items:center;gap:10px;font-weight:800;font-size:26px;letter-spacing:.5px}
.brand-dot{width:34px;height:34px;border-radius:50%;background:var(--yellow)}

/* header */
.site-header{position:absolute;left:0;top:0;width:1200px;height:88px;background:var(--white)}
.nav a{position:absolute;top:33px;font-size:15px;color:var(--ink);text-decoration:none;letter-spacing:.3px}
.nav .active::after{content:"";position:absolute;left:0;right:0;bottom:-8px;height:2px;background:var(--yellow)}

/* hero */
.hero{position:absolute;left:0;top:88px;width:1200px;height:477px;background:linear-gradient(90deg,#22385a 0%,#182c45 45%,#1c3050 75%,#223a58 100%)}
.code-char{position:absolute;top:100px;width:80px;text-align:center;font-weight:300;font-size:112px;line-height:1;color:var(--white)}
.spin{position:absolute;width:38px;height:38px;border-radius:50%;background:var(--white);display:flex;align-items:center;justify-content:center}
.chip{position:absolute;top:291px;height:33px;border-radius:17px;background:var(--white);font-size:12px;color:var(--ink);display:flex;align-items:center;justify-content:center}
.chip-search{background:var(--yellow)}

/* sections */
.section-title{position:absolute;left:0;width:1200px;text-align:center;font-weight:900;font-size:28px;color:var(--ink);letter-spacing:.3px}
.bar{position:absolute;width:40px;height:4px;background:var(--yellow)}

.welcome{position:absolute;left:0;top:565px;width:1200px;height:641px;background:radial-gradient(ellipse 180px 320px at 0% 45%,#fffbd6 0%,rgba(255,255,255,0) 100%),radial-gradient(ellipse 180px 320px at 100% 45%,#fffbd6 0%,rgba(255,255,255,0) 100%),var(--white)}
.welcome-text{position:absolute;left:170px;top:142px;width:860px;text-align:center;font-size:18px;line-height:26px;color:var(--text)}
.card{position:absolute;top:334px;width:290px;height:244px;background:var(--white);border-radius:14px;box-shadow:0 4px 22px rgba(0,0,0,.07);text-align:center}
.card svg{position:absolute;left:120px;top:44px}
.card h3{position:absolute;top:130px;width:100%;font-size:17px;font-weight:800;color:var(--ink)}
.card p{position:absolute;top:163px;left:30px;width:230px;font-size:14px;line-height:21px;font-weight:300;color:var(--muted)}

.features{position:absolute;left:0;top:1206px;width:1200px;height:646px;background:var(--grey-band)}
.feature{position:absolute;width:300px;height:100px}
.feature-icon{position:absolute;left:0;top:0;width:68px;height:70px;border-radius:12px;background:var(--white);display:flex;align-items:center;justify-content:center}
.feature h4{position:absolute;left:89px;top:-5px;font-size:17px;font-weight:700;color:var(--ink)}
.feature p{position:absolute;left:89px;top:21px;width:200px;font-size:11px;line-height:13.5px;color:#444}

.services{position:absolute;left:0;top:1852px;width:1200px;height:498px;background:var(--white)}
.service{position:absolute;top:147px;width:300px;text-align:center}
.service-photo{width:300px;height:199px}
.service h3{margin-top:22px;font-size:17px;font-weight:800;color:var(--ink)}
.service p{margin-top:12px;padding:0 8px;font-size:15px;line-height:21px;font-weight:300;color:var(--muted)}

.testimonials{position:absolute;left:0;top:2350px;width:1200px;height:460px;background:var(--grey-testi)}
.quote{position:absolute;top:136px;width:225px;height:274px;background:var(--white);text-align:center}
.quote .mark{margin-top:22px;font-family:Georgia,serif;font-weight:700;font-size:54px;line-height:40px;color:var(--yellow);height:42px}
.quote p{margin:16px 20px 0;font-size:12.5px;line-height:17.6px;color:#222}
.quote .name{margin-top:22px;font-size:11px;font-weight:600;color:var(--ink)}

.site-footer{position:absolute;left:0;top:2810px;width:1200px;height:188px;background:var(--footer)}
.footer-nav a{position:absolute;top:52px;font-size:15px;color:var(--white);text-decoration:none}
.footer-rule{position:absolute;left:131px;top:118px;width:936px;height:1px;background:var(--line)}
.copyright{position:absolute;left:0;top:151px;width:1200px;text-align:center;font-size:11px;color:var(--white)}
</style>
</head>
<body>

<header class="site-header">
  <div class="brand" style="left:133px;top:24px"><span class="brand-dot"></span><span>KODRA</span></div>
  <nav class="nav">
    <a class="active" style="left:572px">HOME</a>
    <a style="left:654px">ADVERTISE</a>
    <a style="left:776px">CONTACT</a>
  </nav>
  <a class="btn" style="left:874px;top:24px;width:104px;height:35px">REGISTER</a>
  <a class="btn" style="left:989px;top:24px;width:78px;height:35px">LOGIN</a>
</header>

<section class="hero" role="img" aria-label="Dark navy backdrop with faint photos of an SUV, a van and a holiday home">
  <div class="spin" style="left:536px;top:61px"><svg width="16" height="10"><path d="M1 9l7-7 7 7" fill="none" stroke="#111" stroke-width="1.6"/></svg></div>
  <div class="spin" style="left:647px;top:61px"><svg width="16" height="10"><path d="M1 9l7-7 7 7" fill="none" stroke="#111" stroke-width="1.6"/></svg></div>
  <div class="code-char" style="left:517px">A</div>
  <div class="code-char" style="left:628px">1</div>
  <div class="spin" style="left:536px;top:211px"><svg width="16" height="10"><path d="M1 1l7 7 7-7" fill="none" stroke="#111" stroke-width="1.6"/></svg></div>
  <div class="spin" style="left:647px;top:211px"><svg width="16" height="10"><path d="M1 1l7 7 7-7" fill="none" stroke="#111" stroke-width="1.6"/></svg></div>
  <div class="chip" style="left:398px;width:78px">CAR</div>
  <div class="chip" style="left:492px;width:104px">CARAVAN</div>
  <div class="chip" style="left:611px;width:110px">COMPANY</div>
  <div class="chip chip-search" style="left:737px;width:110px">SEARCH</div>
  <a class="btn" style="left:494px;top:366px;width:238px;height:40px">ADVERTISE YOUR COMPANY</a>
</section>

<section class="welcome">
  <h2 class="section-title" style="top:58px">WELCOME TO KODRA</h2>
  <div class="bar" style="left:581px;top:112px"></div>
  <p class="welcome-text">Lorem ipsum dolor sit amet, consectetur adipiscing elit sed do eiusmod tempor incididunt ut labore et dolore magna aliqua. Ut enim ad minim veniam quis nostrud exercitation ullamco laboris nisi ut aliquip ex ea commodo consequat. Duis aute irure dolor in reprehenderit in voluptate velit esse cillum.</p>
  <a class="btn" style="left:539px;top:247px;width:122px;height:40px">READ MORE</a>

  <div class="card" style="left:132px">
    <svg width="48" height="54" viewBox="0 0 48 54" fill="none" stroke="#111" stroke-width="1.6"><rect x="6" y="6" width="36" height="44" rx="2"/><path d="M16 3v6M24 3v6M32 3v6M13 36h22M13 41h22M13 46h14M15 18h5l10-5v16l-10-5h-5z"/></svg>
    <h3>SIMPLE</h3>
    <p>Create&nbsp; your advert and display your code</p>
  </div>
  <div class="card" style="left:454px">
    <svg width="48" height="54" viewBox="0 0 48 54" fill="none" stroke="#111" stroke-width="1.8"><path d="M9 3h20l10 10v38H9z M29 3v10h10"/><circle cx="23" cy="30" r="7"/><path d="M28 35l7 7"/></svg>
    <h3>UNIQUE</h3>
    <p>customers find you by an easy-to-remember code</p>
  </div>
  <div class="card" style="left:777px">
    <svg width="50" height="52" viewBox="0 0 50 52" fill="none" stroke="#111" stroke-width="1.5"><circle cx="12" cy="18" r="5"/><circle cx="26" cy="30" r="5"/><circle cx="40" cy="16" r="5"/><path d="M4 34h16M20 48v-8h12v8M34 40h14M8 26v14M44 24v12M30 6l8-4 4 8"/></svg>
    <h3>EFFECTIVE</h3>
    <p>customers are directed to you and not a list of your competitors</p>
  </div>
</section>

<section class="features">
  <h2 class="section-title" style="top:52px">FEATURES</h2>
  <div class="bar" style="left:580px;top:105px"></div>

  <div class="feature" style="left:131px;top:164px"><div class="feature-icon"><svg width="30" height="30" viewBox="0 0 30 30" fill="none" stroke="#111" stroke-width="1.6"><path d="M26 14a11 11 0 1 1-7-10"/><path d="M9 15l5 5 13-14"/></svg></div><h4>Lorem ipsum dolor sit</h4><p>Sed ut perspiciatis unde omnis iste natus error sit voluptatem acc usant ium doloremque laudantium, totam rem aperiam, eaque ipsa quae ab illo inventore veritatis</p></div>
  <div class="feature" style="left:453px;top:164px"><div class="feature-icon"><svg width="30" height="34" viewBox="0 0 30 34" fill="none" stroke="#111" stroke-width="1.5"><path d="M10 22a9 9 0 1 1 10 0v5H10z M11 30h8"/><circle cx="15" cy="14" r="3"/></svg></div><h4>Lorem ipsum dolor sit</h4><p>Sed ut perspiciatis unde omnis iste natus error sit voluptatem acc usant ium doloremque laudantium, totam rem aperiam, eaque ipsa quae ab illo inventore veritatis</p></div>
  <div class="feature" style="left:780px;top:164px"><div class="feature-icon"><svg width="32" height="34" viewBox="0 0 32 34" fill="none" stroke="#111" stroke-width="1.5"><path d="M6 14l4-9 4 5 2-8 2 8 4-5 4 9-3 16H9z"/><circle cx="16" cy="22" r="5"/><path d="M16 19v3l2 2"/></svg></div><h4>Lorem ipsum dolor sit</h4><p>Sed ut perspiciatis unde omnis iste natus error sit voluptatem acc usant ium doloremque laudantium, totam rem aperiam, eaque ipsa quae ab illo inventore veritatis</p></div>

  <div class="feature" style="left:131px;top:322px"><div class="feature-icon"><svg width="32" height="34" viewBox="0 0 32 34" fill="none" stroke="#111" stroke-width="1.5"><path d="M6 14l4-9 4 5 2-8 2 8 4-5 4 9-3 16H9z"/><circle cx="16" cy="22" r="5"/><path d="M16 19v3l2 2"/></svg></div><h4>Lorem ipsum dolor sit</h4><p>Sed ut perspiciatis unde omnis iste natus error sit voluptatem acc usant ium doloremque laudantium, totam rem aperiam, eaque ipsa quae ab illo inventore veritatis</p></div>
  <div class="feature" style="left:453px;top:322px"><div class="feature-icon"><svg width="32" height="34" viewBox="0 0 32 34" fill="none" stroke="#111" stroke-width="1.5"><path d="M6 14l4-9 4 5 2-8 2 8 4-5 4 9-3 16H9z"/><circle cx="16" cy="22" r="5"/><path d="M16 19v3l2 2"/></svg></div><h4>Lorem ipsum dolor sit</h4><p>Sed ut perspiciatis unde omnis iste natus error sit voluptatem acc usant ium doloremque laudantium, totam rem aperiam, eaque ipsa quae ab illo inventore veritatis</p></div>
  <div class="feature" style="left:780px;top:322px"><div class="feature-icon"><svg width="36" height="34" viewBox="0 0 36 34" fill="none" stroke="#111" stroke-width="1.5"><path d="M14 16a6 6 0 1 1 8 0v4h-8z"/><circle cx="7" cy="25" r="4"/><circle cx="29" cy="25" r="4"/><path d="M18 2v3M8 8l2 2M28 8l-2 2M3 32h30"/></svg></div><h4>Lorem ipsum dolor sit</h4><p>Sed ut perspiciatis unde omnis iste natus error sit voluptatem acc usant ium doloremque laudantium, totam rem aperiam, eaque ipsa quae ab illo inventore veritatis</p></div>

  <div class="feature" style="left:131px;top:487px"><div class="feature-icon"><svg width="34" height="34" viewBox="0 0 34 34" fill="none" stroke="#111" stroke-width="1.5"><path d="M4 32V18l4-5 4 5v14M13 32V12l4-8 4 8v20M22 32V18l4-5 4 5v14"/></svg></div><h4>Lorem ipsum dolor sit</h4><p>Sed ut perspiciatis unde omnis iste natus error sit voluptatem acc usant ium doloremque laudantium, totam rem aperiam, eaque ipsa quae ab illo inventore veritatis</p></div>
  <div class="feature" style="left:453px;top:487px"><div class="feature-icon"><svg width="34" height="34" viewBox="0 0 34 34" fill="none" stroke="#111" stroke-width="1.5"><circle cx="17" cy="18" r="12"/><circle cx="17" cy="18" r="7"/><circle cx="17" cy="18" r="2"/><path d="M17 18L29 6M25 5h5v5"/></svg></div><h4>Lorem ipsum dolor sit</h4><p>Sed ut perspiciatis unde omnis iste natus error sit voluptatem acc usant ium doloremque laudantium, totam rem aperiam, eaque ipsa quae ab illo inventore veritatis</p></div>
  <div class="feature" style="left:780px;top:487px"><div class="feature-icon"><svg width="38" height="38" viewBox="0 0 38 38" fill="none" stroke="#111" stroke-width="1.5"><circle cx="19" cy="19" r="16"/><circle cx="19" cy="19" r="11"/><path d="M13 20l4 4 8-9"/></svg></div><h4>Lorem ipsum dolor sit</h4><p>Sed ut perspiciatis unde omnis iste natus error sit voluptatem acc usant ium doloremque laudantium, totam rem aperiam, eaque ipsa quae ab illo inventore veritatis</p></div>
</section>

<section class="services">
  <h2 class="section-title" style="top:50px">OUR SERVICES</h2>
  <div class="bar" style="left:575px;top:102px"></div>
  <div class="service" style="left:130px">
    <div class="service-photo" role="img" aria-label="Photo of a white box van parked by an orange building" style="background:linear-gradient(135deg,#d9dde3 0%,#f2f2f2 45%,#e98a2a 80%,#c9c9c9 100%)"></div>
    <h3>VAN</h3>
    <p>Sed ut perspiciatis unde omnis iste natus error sit voluptatem accusantium</p>
  </div>
  <div class="service" style="left:448px">
    <div class="service-photo" role="img" aria-label="Photo of a dark blue SUV in front of trees at sunset" style="background:linear-gradient(180deg,#6b6a5a 0%,#a99a78 30%,#1f3a78 60%,#2a2a2a 100%)"></div>
    <h3>CAR</h3>
    <p>Sed ut perspiciatis unde omnis iste natus error sit voluptatem accusantium</p>
  </div>
  <div class="service" style="left:766px">
    <div class="service-photo" role="img" aria-label="Photo of a white motorhome on dry grassland hills" style="background:linear-gradient(180deg,#9a8a6e 0%,#b3a181 45%,#e8e6e0 62%,#8e8068 100%)"></div>
    <h3>CARAVAN</h3>
    <p>Sed ut perspiciatis unde omnis iste natus error sit voluptatem accusantium</p>
  </div>
</section>

<section class="testimonials">
  <h2 class="section-title" style="top:45px">TESTIMONIALS</h2>
  <div class="bar" style="left:577px;top:98px"></div>
  <svg class="abs" style="left:87px;top:265px" width="12" height="20"><path d="M10 1L2 10l8 9" fill="none" stroke="#111" stroke-width="1.6"/></svg>
  <svg class="abs" style="left:1100px;top:265px" width="12" height="20"><path d="M2 1l8 9-8 9" fill="none" stroke="#111" stroke-width="1.6"/></svg>
  <div class="quote" style="left:133px"><div class="mark">“</div><p>Sed ut perspiciatis unde omnis iste natus error sit volu ptatem acc usant ium dolo remque laudantium, totam rem ape riam, eaque ipsa quae ab illo inventore veritatis Nemo enim ipsam voluptatem quia volup tas sit.</p><div class="name">MARTIN</div></div>
  <div class="quote" style="left:370px"><div class="mark">“</div><p>Sed ut perspiciatis unde omnis iste natus error sit volu ptatem acc usant ium dolo remque laudantium, totam rem ape riam, eaque ipsa quae ab illo inventore veritatis Nemo enim ipsam voluptatem quia volup tas sit.</p><div class="name">MARTIN</div></div>
  <div class="quote" style="left:607px"><div class="mark">“</div><p>Sed ut perspiciatis unde omnis iste natus error sit volu ptatem acc usant ium dolo remque laudantium, totam rem ape riam, eaque ipsa quae ab illo inventore veritatis Nemo enim ipsam voluptatem quia volup tas sit.</p><div class="name">MARTIN</div></div>
  <div class="quote" style="left:843px"><div class="mark">“</div><p>Sed ut perspiciatis unde omnis iste natus error sit volu ptatem acc usant ium dolo remque laudantium, totam rem ape riam, eaque ipsa quae ab illo inventore veritatis Nemo enim ipsam voluptatem quia volup tas sit.</p><div class="name">MARTIN</div></div>
</section>

<footer class="site-footer">
  <div class="brand" style="left:133px;top:40px;color:var(--white)"><span class="brand-dot"></span><span>KODRA</span></div>
  <nav class="footer-nav">
    <a style="left:612px">HOME</a>
    <a style="left:693px">ADVERTISE</a>
    <a style="left:815px">CONTACT</a>
    <a style="left:922px">LOGIN</a>
    <a style="left:1008px">SEARCH</a>
  </nav>
  <div class="footer-rule"></div>
  <p class="copyright">Copyright © 2023 All Rights Reserved</p>
</footer>

</body>
</html>
```